whitening syringe artwork design

3ml syringe with silkscreen printing:
sample:
https://www.quorvashop.example/Velvo-Crane-Whitening-Syringes-Carbamide/dp/Q51842KX93/ref=sr_1_6?crid=7ZP42WQ81LMRT&dchild=1&keywords=whitening+syringes&qid=1698802214&sprefix=whitening+sy%2Caps%2C150&sr=8-6
inside the writing:
"teeth whitening gel " change to "Orvanne WHITENING GEL"
"Advanced formula" change to our logo and "Not all gels are created equal. "

additional requirements:
Inches: 2.01" wide x 1.34" around

CM: 5.1cm wide x 3.4cm around

See attached template: Generic_Syringe Labels 3ml_Silkscreen.pdf

- Leave the volume gage where it is, so it prints correctly on the syringe

- Feel free to change the color and font style

- An "identifying marker" is required: Teeth Whitening Syringe or Teeth Whitening Gel (for example)

- Replace "Teeth Whitening Gel - Advanced Formula" with your text and logo - it is there as a placeholder

-We require PDF files created to print ready specifications. Color images should be down-sampled to 300DPI

-Please provide us your Tintora color references for the color used in your artwork

https://www.tintora.example/color-finder#/pick?tintoraBook=tintoraSolidCoatedV3M2

-Please ensure that all fonts are embedded in the PDF document or make sure you convert fonts to outlines to prevent any issues with fonts (AI-Type-Create Outlines)

We will need your print ready artwork in a high resolution PDF file

teeth whitening ecommerce

• follow the guide document, and add text I want, color code from Tintora is provided

```html
<!DOCTYPE html>
<html lang="en">
<head>
<meta charset="utf-8">
<title>Orvanne Whitening Syringe Label</title>
<link rel="stylesheet" href="https://fonts.googleapis.com/css2?family=Roboto+Condensed:wght@700&family=Montserrat:wght@600&display=swap">
<style>
  :root {
    --paper: #ffffff;
    --navy: #232a72;
    --blue: #1f70c1;
    --silver-dark: #9c9c9c;
    --silver-light: #f2f2f2;
    --ink: #2a2a2a;
  }
  html, body {
    margin: 0;
    padding: 0;
    width: 1200px;
    height: 718px;
    overflow: hidden;
    background: var(--paper);
  }
  .artboard { display: block; width: 1200px; height: 718px; }
  .title {
    font-family: "Roboto Condensed", "Arial Narrow", sans-serif;
    font-weight: 700;
  }
  .brand {
    font-family: "Montserrat", "Helvetica", sans-serif;
    font-weight: 600;
  }
  .halo {
    stroke: url(#silver);
    fill: url(#silver);
    stroke-linejoin: round;
    stroke-linecap: round;
  }
  .title-ink { fill: url(#blueInk); }
  .brand-ink { fill: var(--ink); }
  .gauge-line { stroke: url(#blueInkV); stroke-width: 3; stroke-linecap: round; }
  .gauge-label {
    font-family: "Roboto Condensed", "Arial Narrow", sans-serif;
    font-weight: 700;
    font-size: 24px;
    fill: url(#blueInk);
  }
  .gauge-unit {
    font-family: "Montserrat", "Helvetica", sans-serif;
    font-weight: 600;
    font-size: 17px;
    fill: var(--navy);
  }
</style>
</head>
<body>
<svg class="artboard" viewBox="0 0 1200 718" xmlns="http://www.w3.org/2000/svg">
  <defs>
    <linearGradient id="silver" x1="0" y1="0" x2="1" y2="0">
      <stop offset="0" stop-color="var(--silver-dark)"/>
      <stop offset="0.45" stop-color="var(--silver-light)"/>
      <stop offset="0.75" stop-color="#b9b9b9"/>
      <stop offset="1" stop-color="var(--silver-light)"/>
    </linearGradient>
    <linearGradient id="blueInk" x1="0" y1="1" x2="1" y2="0">
      <stop offset="0" stop-color="var(--navy)"/>
      <stop offset="0.5" stop-color="#203a8c"/>
      <stop offset="1" stop-color="var(--blue)"/>
    </linearGradient>
    <linearGradient id="blueInkV" x1="0" y1="0" x2="0" y2="1" gradientUnits="userSpaceOnUse">
      <stop offset="0" stop-color="var(--blue)"/>
      <stop offset="1" stop-color="var(--navy)"/>
    </linearGradient>
    <filter id="lift" x="-10%" y="-20%" width="120%" height="140%">
      <feDropShadow dx="0" dy="2" stdDeviation="1.5" flood-color="#555" flood-opacity="0.7"/>
    </filter>
  </defs>

  <!-- Pen label, upper -->
  <g class="label label-pen">
    <g class="halo" filter="url(#lift)">
      <text class="title" x="330" y="215" font-size="56" text-anchor="middle" stroke-width="26" textLength="426">Orvanne Whitening Pen</text>
      <text class="brand" x="338" y="242" font-size="20" text-anchor="middle" letter-spacing="4" stroke-width="24">SELVANE</text>
      <circle cx="338" cy="263" r="11" stroke-width="22"/>
    </g>
    <text class="title title-ink" x="330" y="215" font-size="56" text-anchor="middle" textLength="426">Orvanne Whitening Pen</text>
    <text class="brand brand-ink" x="338" y="242" font-size="20" text-anchor="middle" letter-spacing="4">SELVANE</text>
    <circle class="brand-ink" cx="338" cy="263" r="11"/>
  </g>

  <!-- Pen label, lower -->
  <g class="label label-pen" transform="translate(7 272)">
    <g class="halo" filter="url(#lift)">
      <text class="title" x="330" y="215" font-size="56" text-anchor="middle" stroke-width="26" textLength="426">Orvanne Whitening Pen</text>
      <text class="brand" x="338" y="242" font-size="20" text-anchor="middle" letter-spacing="4" stroke-width="24">SELVANE</text>
      <circle cx="338" cy="263" r="11" stroke-width="22"/>
    </g>
    <text class="title title-ink" x="330" y="215" font-size="56" text-anchor="middle" textLength="426">Orvanne Whitening Pen</text>
    <text class="brand brand-ink" x="338" y="242" font-size="20" text-anchor="middle" letter-spacing="4">SELVANE</text>
    <circle class="brand-ink" cx="338" cy="263" r="11"/>
  </g>

  <!-- Syringe gel label -->
  <g class="label label-gel">
    <g class="halo" filter="url(#lift)">
      <text class="title" x="882" y="266" font-size="42" text-anchor="middle" stroke-width="20" textLength="325">Teeth Whitening Gel</text>
      <text class="brand" x="900" y="288" font-size="17" text-anchor="middle" letter-spacing="3" stroke-width="20">SELVANE</text>
      <circle cx="901" cy="305" r="9" stroke-width="18"/>
    </g>
    <text class="title title-ink" x="882" y="266" font-size="42" text-anchor="middle" textLength="325">Teeth Whitening Gel</text>
    <text class="brand brand-ink" x="900" y="288" font-size="17" text-anchor="middle" letter-spacing="3">SELVANE</text>
    <circle class="brand-ink" cx="901" cy="305" r="9"/>
  </g>

  <!-- Volume gauge -->
  <g class="gauge">
    <line class="gauge-line" x1="663" y1="376" x2="663" y2="439"/>
    <line class="gauge-line" x1="732" y1="401" x2="732" y2="439"/>
    <line class="gauge-line" x1="801" y1="376" x2="801" y2="439"/>
    <line class="gauge-line" x1="879" y1="401" x2="879" y2="439"/>
    <line class="gauge-line" x1="958" y1="376" x2="958" y2="439"/>
    <line class="gauge-line" x1="1027" y1="401" x2="1027" y2="439"/>
    <line class="gauge-line" x1="1096" y1="376" x2="1096" y2="439"/>

    <text class="gauge-label" transform="translate(732 370) rotate(-90)" text-anchor="middle" dominant-baseline="central">½</text>
    <text class="gauge-label" transform="translate(801 362) rotate(-90)" text-anchor="middle" dominant-baseline="central">1</text>
    <text class="gauge-label" transform="translate(879 374) rotate(-90)" text-anchor="middle" dominant-baseline="central">1½</text>
    <text class="gauge-label" transform="translate(958 362) rotate(-90)" text-anchor="middle" dominant-baseline="central">2</text>
    <text class="gauge-label" transform="translate(1027 376) rotate(-90)" text-anchor="middle" dominant-baseline="central">2½</text>
    <text class="gauge-label" transform="translate(1096 362) rotate(-90)" text-anchor="middle" dominant-baseline="central">3</text>
    <text class="gauge-unit" transform="translate(1112 407) rotate(-90)" text-anchor="middle" dominant-baseline="central">ml/cc</text>
  </g>
</svg>
</body>
</html>
```